Business Card for Vorla Parts Wholesale supplier

Hi There! I need a new business card for our company. We are specialized in selling Vorla parts, mostly we sell new LCD screens for Zelnar and Drelks. I would like to see that back in the design.

You can find the colors and logo's on our website: www.hartuvo.nl

Industry/Entity Type

Business

Contact Information for Business Card

My Details:
Tobias Lindqvist

Phone: 0031687203316
E-mail: Tobias@hartuvo.nl

Slogan: "Because Quality Matters"

Font styles to use
Sans Serif

Colors

Designer to choose colors to be used in the design.

Requirements
Must have
• A Black backside with the Hartuvo logo on it. The front side should be clean with only my contact details.
• But I'm also open for something really different or awesome!
Nice to have
• Remember that we are in the parts & repairing industry, So i'll be handing those business cards mainly to repair companies. Maybe you can do something with that thought :)

```html
<!DOCTYPE html>
<html lang="en">
<head>
<meta charset="utf-8">
<title>Hartuvo Business Card</title>
<link href="https://fonts.googleapis.com/css2?family=Open+Sans:ital,wght@0,400;0,700;1,400&display=swap" rel="stylesheet">
<style>
  :root {
    --backdrop: #2b2b2d;
    --card-white: #ffffff;
    --brand-orange: #f2711c;
    --brand-orange-light: #f7913a;
    --ink-black: #141414;
    --card-black: #0c0c0c;
    --card-black-soft: #262626;
    --text-white: #ffffff;
  }
  * { margin: 0; padding: 0; box-sizing: border-box; }
  html, body {
    width: 1200px;
    height: 950px;
    overflow: hidden;
    background: var(--backdrop);
    font-family: "Open Sans", Arial, sans-serif;
  }
  .canvas {
    width: 1200px;
    height: 950px;
    display: flex;
    flex-direction: column;
    align-items: center;
    justify-content: center;
    gap: 50px;
  }
  .card {
    width: 700px;
    height: 400px;
    border-radius: 4px;
    overflow: hidden;
    position: relative;
    box-shadow: 0 10px 30px rgba(0,0,0,0.45);
  }

  /* Front side */
  .card-front {
    background: var(--card-white);
    display: flex;
    flex-direction: column;
  }
  .front-brand {
    flex: 0 0 60%;
    display: flex;
    align-items: center;
    padding-left: 150px;
  }
  .front-details {
    flex: 1;
    background: linear-gradient(180deg, var(--brand-orange) 0%, var(--brand-orange-light) 100%);
    color: var(--text-white);
    display: flex;
    flex-direction: column;
    justify-content: center;
    padding-left: 150px;
    gap: 10px;
  }
  .contact-name {
    font-weight: 700;
    font-size: 30px;
    letter-spacing: 0.3px;
  }
  .contact-line {
    font-size: 16px;
    font-weight: 400;
    letter-spacing: 0.3px;
  }
  .contact-line .divider { margin: 0 6px; }

  /* Logo lockup */
  .brand-lockup {
    display: flex;
    align-items: center;
    gap: 16px;
  }
  .brand-dot {
    width: 62px;
    height: 62px;
    border-radius: 50%;
    background: var(--brand-orange);
    flex: 0 0 auto;
  }
  .brand-name {
    font-weight: 700;
    font-size: 72px;
    line-height: 1;
    letter-spacing: -1px;
    color: var(--ink-black);
  }

  /* Back side */
  .card-back {
    background: linear-gradient(125deg, var(--card-black-soft) 0%, var(--card-black) 55%, var(--card-black) 100%);
    display: flex;
    flex-direction: column;
    justify-content: center;
    padding-left: 150px;
    gap: 18px;
  }
  .card-back .brand-name { color: var(--text-white); }
  .slogan {
    font-style: italic;
    font-size: 18px;
    color: var(--brand-orange);
    padding-left: 2px;
  }
</style>
</head>
<body>
<main class="canvas">
  <section class="card card-front" aria-label="Business card front">
    <div class="front-brand">
      <div class="brand-lockup">
        <span class="brand-dot"></span>
        <span class="brand-name">hartuvo</span>
      </div>
    </div>
    <div class="front-details">
      <p class="contact-name">Tobias Lindqvist</p>
      <p class="contact-line">0031687203316<span class="divider">|</span>Tobias@hartuvo.nl<span class="divider">|</span>www.hartuvo.nl</p>
    </div>
  </section>

  <section class="card card-back" aria-label="Business card back">
    <div class="brand-lockup">
      <span class="brand-dot"></span>
      <span class="brand-name">hartuvo</span>
    </div>
    <p class="slogan">Because Quality Matters</p>
  </section>
</main>
</body>
</html>
```